Climbing Gear Company Stationary Design

We need some new stationary to standardise our business.
We require:

Business Card
A4 Letterhead
With complements slip

Our business is a Distributor and retailer of rock climbing equipment throughout Australia.
We need to the stationary (business card in particular) to reflect this.

Target Market(s)

customers, other retail outlets, overseas manufacturers.

Industry/Entity Type

Business

Requirements
Must have
• company logo
website url- www.ridgetopgearworks.com.au
email - mark@ridgetopgearworks.com
Business Address: Unit 3, 14-16 Marlowe Street, Kestrel Bay, North Coast, 2371
Phone: 0438 627 194
my Name (on Business card) - Gordon Pellimore
use of Blue colour in our logo

```html
<!DOCTYPE html>
<html lang="en">
<head>
<meta charset="utf-8">
<title>Ridgetop Gearworks – Business Card</title>
<link rel="stylesheet" href="https://fonts.googleapis.com/css2?family=Open+Sans:wght@400;600;700;800&display=swap">
<style>
  :root {
    --brand-blue: #263f8e;
    --band-blue: #2d4793;
    --band-glow: #7d8cc0;
    --card-white: #ffffff;
    --rule-grey: #9a9a9a;
    --ink-dark: #2b2b2b;
    --page-bg: #e9e9e9;
  }
  * { margin: 0; padding: 0; box-sizing: border-box; }
  html, body {
    width: 1200px;
    height: 1094px;
    overflow: hidden;
    background: var(--page-bg);
    font-family: "Open Sans", sans-serif;
  }
  .card {
    position: absolute;
    width: 784px;
    height: 448px;
    background: var(--card-white);
    border-radius: 26px;
    overflow: hidden;
    box-shadow: 0 2px 6px rgba(0,0,0,0.18);
  }
  .card-front { left: 187px; top: 78px; }
  .card-back  { left: 178px; top: 577px; }

  .wordmark {
    position: absolute;
    left: 0; right: 0;
    text-align: center;
    font-weight: 800;
    font-size: 50px;
    letter-spacing: 1px;
    color: var(--brand-blue);
    line-height: 1;
  }
  .tagline {
    position: absolute;
    left: 0; right: 0;
    text-align: center;
    font-weight: 600;
    font-size: 21px;
    letter-spacing: 4px;
    color: var(--brand-blue);
    line-height: 1;
    white-space: nowrap;
  }
  .card-front .wordmark { top: 60px; }
  .card-front .tagline  { top: 128px; }

  .address {
    position: absolute;
    top: 210px; left: 0; right: 0;
    text-align: center;
    font-size: 19px;
    letter-spacing: 1.4px;
    color: var(--ink-dark);
    white-space: nowrap;
  }
  .rule {
    position: absolute;
    left: 0; right: 0;
    top: 244px;
    height: 3px;
    background: var(--rule-grey);
  }
  .contact-band {
    position: absolute;
    left: 0; right: 0;
    top: 255px; bottom: 0;
    background: radial-gradient(ellipse 42% 90% at 48% 35%, var(--band-glow) 0%, var(--band-blue) 100%);
  }
  .holder-name {
    position: absolute;
    right: 434px;
    top: 78px;
    font-weight: 700;
    font-size: 18px;
    color: var(--card-white);
    white-space: nowrap;
  }
  .band-divider {
    position: absolute;
    left: 363px;
    top: 38px;
    width: 2px;
    height: 128px;
    background: var(--card-white);
  }
  .contact-list {
    position: absolute;
    left: 392px;
    top: 58px;
    list-style: none;
  }
  .contact-list li {
    display: flex;
    align-items: center;
    height: 25.5px;
    font-size: 16px;
    color: var(--card-white);
    white-space: nowrap;
  }
  .contact-list svg {
    width: 15px; height: 15px;
    margin-right: 10px;
    flex: none;
  }

  .card-back .wordmark { top: 139px; }
  .card-back .tagline  { top: 220px; }
  .back-url {
    position: absolute;
    left: 0; right: 0;
    top: 396px;
    text-align: center;
    font-size: 19px;
    letter-spacing: 1.6px;
    color: var(--ink-dark);
  }
</style>
</head>
<body>
  <section class="card card-front">
    <div class="wordmark">RIDGETOP GEARWORKS</div>
    <div class="tagline">ROPE•RACK•ROCK ACROSS AUSTRALIA</div>
    <p class="address">Unit 3, 14-16 Marlowe Street, Kestrel Bay, North Coast, 2371</p>
    <div class="rule"></div>
    <div class="contact-band">
      <p class="holder-name">Gordon Pellimore</p>
      <div class="band-divider"></div>
      <ul class="contact-list">
        <li>
          <svg viewBox="0 0 16 16" aria-hidden="true"><circle cx="8" cy="8" r="7" fill="none" stroke="#fff" stroke-width="1.4"/><path d="M5.5 4.5 L7 4.5 L7.6 6.4 L6.7 7.2 C7.2 8.3 7.8 8.9 8.8 9.4 L9.6 8.5 L11.5 9.1 L11.5 10.6 C8 11 5 8 5.5 4.5 Z" fill="#fff"/></svg>
          0438 627 194
        </li>
        <li>
          <svg viewBox="0 0 16 16" aria-hidden="true"><rect x="1.5" y="3.5" width="13" height="9" fill="#fff"/><path d="M1.5 3.5 L8 9 L14.5 3.5" fill="none" stroke="#2d4793" stroke-width="1.2"/></svg>
          mark@ridgetopgearworks.com
        </li>
        <li>
          <svg viewBox="0 0 16 16" aria-hidden="true"><circle cx="8" cy="8" r="6.5" fill="#fff"/><path d="M1.5 8 H14.5 M8 1.5 C5 5 5 11 8 14.5 M8 1.5 C11 5 11 11 8 14.5" fill="none" stroke="#2d4793" stroke-width="1"/></svg>
          www.ridgetopgearworks.com.au
        </li>
      </ul>
    </div>
  </section>

  <section class="card card-back">
    <div class="wordmark">RIDGETOP GEARWORKS</div>
    <div class="tagline">ROPE•RACK•ROCK ACROSS AUSTRALIA</div>
    <p class="back-url">www.ridgetopgearworks.com.au</p>
  </section>
</body>
</html>
```